Brochure for dynamic theatrical production company

New brochure for Heron Stageworks, featuring our current theatrical projects. We are a theatrical producing and consulting company, and we need the brochure to communicate the breadth of our projects. Our work is produced and performed throughtout the United States and also tours to Europe, Asia, the Middle East and South America. We also work with companies and artists from around the globe and bring them to the United States to tour and develop new work. Projects range from experimental multi-disciplinary works to Broadway musicals.

The brochure is meant to introduce other performing arts professionals to our work. These potential clients might engage one of our artists or projects for a performance, or they may engage us as consultants on additional projects.

The final design should be a standard size document that is fairly simple and inexpensive to reproduce. This is a piece that is used within the entertainment industry to develop interest in our work from other theaters, presenters, festivals, donors and artists.

I have included the pdf of last year's design, as well as a word document with the text to be used for this year. The world document also contains a link to a dropbox folder with photos and other supplementary materials as well.

You can also refer to our website for insights into our work and our aesthetic. www.heronstageworks-example.com

Target Market(s)

Industry professionals, funders/investors, prospective clients.

Industry/Entity Type

Entertainment Industry

Font styles to use
Sans Serif

Colors

Designer to choose colors to be used in the design.

Requirements
Must have
• Please use text provided in "Heron Brochure 2018" document. A variety of photos and other graphics are available for download via a link embedded in the document.
• Please make sure the finished piece can be printed on standard paper sizes in the US: For example: ledger size is 279 x 432 mm (11.0 x 17.0 in), letter size is 216 x 279 mm (8.5 x 11.0 in), Legal size is 216 x 356 mm (8.5 x 14.0 in)
Nice to have
• Our previous brochure and current website use pictures in the shape of circles (see sample attached). I would like that to be consistent with the new brochure. Website, for your reference, is www.heronstageworks-example.com
Should not have
• non-standard paper sizes

```html
<!DOCTYPE html>
<html lang="en">
<head>
<meta charset="utf-8">
<title>Heron Stageworks – Contact Panel</title>
<link href="https://fonts.googleapis.com/css2?family=Jost:wght@400;600&display=swap" rel="stylesheet">
<style>
  :root {
    --teal: #0aa0aa;
    --ink: #141414;
    --mist: #e4e0de;
    --ring: #dcdcdc;
    --paper: #ffffff;
  }
  html, body {
    margin: 0;
    padding: 0;
    overflow: hidden;
    background: var(--paper);
  }
  .panel {
    position: relative;
    width: 1200px;
    height: 852px;
    overflow: hidden;
    background: var(--paper);
    font-family: "Jost", sans-serif;
    color: var(--ink);
  }
  .shapes {
    position: absolute;
    inset: 0;
  }
  .contacts {
    position: absolute;
    left: 113px;
    top: 0;
    width: 400px;
    text-align: center;
  }
  .contacts__intro {
    position: absolute;
    top: 82px;
    width: 100%;
    font-size: 15px;
    line-height: 22px;
    letter-spacing: 0.04em;
    margin: 0;
  }
  .person {
    position: absolute;
    width: 100%;
    margin: 0;
  }
  .person__name {
    display: block;
    font-weight: 600;
    font-size: 25px;
    letter-spacing: 0.06em;
    color: var(--teal);
    line-height: 30px;
  }
  .person__role {
    display: block;
    font-size: 19px;
    letter-spacing: 0.05em;
    color: var(--teal);
    line-height: 26px;
    margin-top: 2px;
  }
  .person__line {
    display: block;
    font-size: 19px;
    letter-spacing: 0.03em;
    line-height: 27px;
    margin-top: 4px;
  }
  .person__line + .person__line { margin-top: 0; }
  .person--lead { top: 166px; }
  .person--associate { top: 332px; }
  .person--coordinator { top: 499px; }

  .visit {
    position: absolute;
    left: 135px;
    top: 739px;
    width: 356px;
    text-align: center;
    color: var(--paper);
    font-weight: 600;
    font-size: 22px;
    letter-spacing: 0.06em;
    margin: 0;
  }
  .brand {
    position: absolute;
    left: 662px;
    top: 758px;
    display: flex;
    align-items: center;
    gap: 12px;
  }
  .brand__dot {
    width: 22px;
    height: 22px;
    border-radius: 50%;
    background: var(--teal);
  }
  .brand__name {
    font-size: 34px;
    font-weight: 400;
    color: var(--ink);
    letter-spacing: 0.01em;
  }
  .tagline {
    position: absolute;
    right: 25px;
    top: 770px;
    text-align: right;
    margin: 0;
  }
  .tagline__text {
    display: block;
    font-size: 15px;
    letter-spacing: 0.08em;
    color: var(--teal);
    line-height: 20px;
  }
  .tagline__url {
    display: block;
    font-size: 12px;
    letter-spacing: 0.04em;
    margin-top: 2px;
  }
</style>
</head>
<body>
<main class="panel">
  <svg class="shapes" width="1200" height="852" viewBox="0 0 1200 852" aria-hidden="false">
    <defs>
      <clipPath id="hero-clip">
        <circle cx="902" cy="225" r="433"/>
      </clipPath>
      <radialGradient id="hero-tone" cx="0.55" cy="0.45" r="0.7">
        <stop offset="0" stop-color="#d9a56f"/>
        <stop offset="0.5" stop-color="#9a6a4c"/>
        <stop offset="1" stop-color="#4a3730"/>
      </radialGradient>
    </defs>
    <circle class="accent accent--corner" cx="-9" cy="-9" r="148" fill="var(--mist)"/>
    <circle class="accent accent--top" cx="660" cy="-40" r="190" fill="var(--mist)"/>
    <circle class="accent accent--band" cx="911" cy="243" r="446" fill="var(--teal)"/>
    <g role="img" aria-label="Stage photograph: an ensemble of costumed performers dancing under string lights, with musicians playing behind them">
      <rect x="0" y="0" width="1200" height="852" fill="url(#hero-tone)" clip-path="url(#hero-clip)"/>
    </g>
    <circle class="accent accent--ring" cx="313" cy="866" r="243" fill="none" stroke="var(--ring)" stroke-width="1.2"/>
    <circle class="accent accent--visit" cx="313" cy="816" r="178" fill="var(--teal)"/>
  </svg>

  <section class="contacts">
    <p class="contacts__intro">For more information,<br>please contact:</p>

    <p class="person person--lead">
      <span class="person__name">Lena Marsh</span>
      <span class="person__role">Executive/Creative Producer</span>
      <span class="person__line">lena@heronstageworks-example.com</span>
      <span class="person__line">(555) 014 - 2287</span>
    </p>

    <p class="person person--associate">
      <span class="person__name">Tavi Okafor</span>
      <span class="person__role">Associate Producer</span>
      <span class="person__line">tavi@heronstageworks-example.com</span>
      <span class="person__line">(555) 018 - 6630</span>
    </p>

    <p class="person person--coordinator">
      <span class="person__name">Owen Pratt</span>
      <span class="person__role">Production Coordinator</span>
      <span class="person__line">owen@heronstageworks-example.com</span>
    </p>
  </section>

  <p class="visit">or visit:</p>

  <div class="brand">
    <span class="brand__dot"></span>
    <span class="brand__name">Heron Stageworks</span>
  </div>

  <p class="tagline">
    <span class="tagline__text">CREATIVE PRODUCING</span>
    <span class="tagline__text">AND CONSULTING</span>
    <span class="tagline__url">www.heronstageworks-example.com</span>
  </p>
</main>
</body>
</html>
```